4D Cradle Glimpse Luxury Ultrasound Billboard

Design a HIGH-END, MODERN billboard for my private prenatal ultrasound studio, 4D Cradle Glimpse, located in Cedar Cove, Sealand.
This billboard will be viewed by drivers traveling at highway speeds, so it must be extremely clean, simple, and readable within 6 seconds.
About My Business
4D Cradle Glimpse is a private prenatal ultrasound studio specializing in:
Highest technology 4D/HD Ultrasounds
Early Gender Determination
Pregnancy Confirmation
I have been serving families for nearly 10 years and is known for creating a memorable experience, not just an ultrasound appointment.
Design Style
I DO NOT want:
Flowers
Leaves
Swirls
Glitter
Hearts everywhere
Busy backgrounds
Generic maternity stock graphics
I DO want:
Modern
Luxury
Upscale
Clean
Professional
Eye-catching
Premium medical spa feel
Colors
Use colors from my logo:
LOGO Green ( or a deep green)
Black
White
Soft Gold accents
Images:
Incorporate my professional headshot in a clean, modern way, logo, and the ultrasound images
Text
Keep wording minimal.
Primary Headline ( OPEN TO IDEAS) :
EXAMPLES ( WOULD RATHER SOMETHING MORE CATCHY)
" ADVANCED IMAGING. UNFORGETTABLE MOMENTS"
"MEET YOUR BABY BEFORE BIRTH"
Under headline:
4D Ultrasound • Early Gender • Pregnancy Confirmation
Business Name:
4D Cradle Glimpse
Private Prenatal Ultrasound Studio
Phone Number:
850-471-5923
Important
This billboard must be readable in 5–6 seconds from a moving vehicle.
Less text is better.
The phone number and business name must be visible from a distance.
The design should feel like a premium brand that immediately tells expecting parents:
“This is where I go to see my baby.”
Files Provided
Official logo
Headshot
Ultrasound images
Don’t make this look like a medical office billboard.
Make it look like a luxury baby experience billboard. That’s what separates 4D Cradle Glimpse from hospitals, OB offices, and all the new studios popping up around you. The emotional connection is what gets moms to book. ❤️
Billboard Size - 10.6” x 36”

```html
<!DOCTYPE html>
<html lang="en">
<head>
<meta charset="utf-8">
<title>4D Cradle Glimpse Billboard</title>
<link rel="stylesheet" href="https://fonts.googleapis.com/css2?family=Montserrat:wght@400;500;600;700&family=Playfair+Display:wght@700&family=Mrs+Saint+Delafield&family=Roboto:wght@500&display=swap">
<style>
  :root {
    --page: #ffffff;
    --cream: #f7f2eb;
    --forest: #2c3a31;
    --forest-deep: #1c2621;
    --ink: #1a1a1a;
    --gold: #d4a04a;
    --gold-light: #ecc26a;
    --gold-dark: #a8732c;
    --white: #ffffff;
  }
  * { margin: 0; padding: 0; box-sizing: border-box; }
  html, body {
    width: 1200px; height: 647px; overflow: hidden;
    background: var(--page);
  }
  .page { position: relative; width: 1200px; height: 647px; }

  .revision-note {
    position: absolute; right: 58px; top: 58px;
    font-family: "Roboto", sans-serif; font-weight: 500;
    font-size: 40px; color: var(--gold); letter-spacing: 0.5px;
  }

  .billboard {
    position: absolute; left: 52px; top: 180px;
    width: 1097px; height: 323px; overflow: hidden;
    background: var(--cream);
  }
  .billboard-shapes { position: absolute; inset: 0; }

  .headshot {
    position: absolute; left: 63px; top: 9px; width: 192px; height: 314px;
    border-radius: 96px 96px 0 0;
    background: linear-gradient(180deg, #cdb489 0%, #b89a72 30%, #4d6a4b 60%, #2f4a33 100%);
  }

  .eyebrow {
    position: absolute; left: 0; width: 1127px; top: 8px; text-align: center;
    font-family: "Montserrat", sans-serif; font-weight: 500;
    font-size: 36px; line-height: 1.1; letter-spacing: 3px; color: var(--forest);
  }
  .headline {
    position: absolute; left: 344px; width: 438px; top: 14px; text-align: center;
    font-family: "Playfair Display", serif; font-weight: 700;
    font-size: 150px; line-height: 1.1; letter-spacing: 8px;
    background: linear-gradient(180deg, var(--gold-dark) 0%, var(--gold-light) 48%, var(--gold-dark) 100%);
    -webkit-background-clip: text; background-clip: text; color: transparent;
  }
  .sub-script {
    position: absolute; left: 406px; width: 314px; top: 166px; text-align: center;
    font-family: "Mrs Saint Delafield", cursive; font-size: 64px; line-height: 1;
    color: var(--ink);
  }
  .rule {
    position: absolute; top: 197px; width: 84px; height: 2px;
    background: linear-gradient(90deg, transparent, var(--gold), transparent);
  }
  .rule--left { left: 321px; }
  .rule--right { left: 720px; }

  .scan-image {
    position: absolute; left: 818px; top: 18px; width: 185px; height: 202px;
    border: 4px solid var(--gold); border-radius: 16px;
    background: radial-gradient(ellipse at 30% 50%, #b87466 0%, #8a4b40 45%, transparent 70%),
                radial-gradient(ellipse at 75% 50%, #b87466 0%, #8a4b40 45%, transparent 70%),
                #2a1512;
  }

  .services {
    position: absolute; left: 366px; top: 246px; list-style: none;
    font-family: "Montserrat", sans-serif; font-weight: 600;
    font-size: 13px; line-height: 1; letter-spacing: 0.6px; color: var(--white);
  }
  .services li { position: relative; margin-bottom: 7px; }
  .services li::before {
    content: ""; position: absolute; left: -15px; top: 4px;
    width: 5px; height: 5px; border-radius: 50%; background: var(--gold);
  }
  .services .two-line { line-height: 0.95; }

  .brand-card {
    position: absolute; left: 517px; top: 235px; width: 158px; height: 78px;
    background: var(--white); border: 2px solid var(--forest); border-radius: 10px;
    display: flex; flex-direction: column; align-items: center; justify-content: center;
    text-align: center;
  }
  .brand-name {
    font-family: "Montserrat", sans-serif; font-weight: 700;
    font-size: 14px; line-height: 1.1; color: var(--forest);
  }
  .brand-tagline {
    margin-top: 9px;
    font-family: "Montserrat", sans-serif; font-weight: 500;
    font-size: 6.3px; letter-spacing: 0.3px; color: var(--forest);
  }

  .phone-icon { position: absolute; left: 706px; top: 261px; width: 44px; height: 44px; }
  .phone-number {
    position: absolute; left: 764px; top: 258px;
    font-family: "Montserrat", sans-serif; font-weight: 700;
    font-size: 34px; line-height: 1; letter-spacing: 0.5px; color: var(--white);
  }
  .location {
    position: absolute; left: 768px; top: 292px; width: 220px;
    display: flex; align-items: center; gap: 8px;
    font-family: "Montserrat", sans-serif; font-weight: 500;
    font-size: 11px; color: var(--gold); white-space: nowrap;
  }
  .location::before, .location::after {
    content: ""; flex: 1; height: 1px; background: var(--gold);
  }
</style>
</head>
<body>
<div class="page">
  <div class="revision-note">REVISED (SPACING)</div>

  <section class="billboard">
    <svg class="billboard-shapes" viewBox="0 0 1097 323" width="1097" height="323" aria-hidden="true">
      <defs>
        <linearGradient id="panelGreen" x1="0" y1="0" x2="1" y2="1">
          <stop offset="0" stop-color="#26302a"/>
          <stop offset="1" stop-color="#354639"/>
        </linearGradient>
        <linearGradient id="goldFade" x1="0" y1="0" x2="1" y2="1">
          <stop offset="0" stop-color="#d4a04a"/>
          <stop offset="0.7" stop-color="#f7f2eb" stop-opacity="0"/>
        </linearGradient>
        <linearGradient id="goldEdge" x1="0" y1="0" x2="0" y2="1">
          <stop offset="0" stop-color="#a8732c"/>
          <stop offset="0.5" stop-color="#ecc26a"/>
          <stop offset="1" stop-color="#a8732c"/>
        </linearGradient>
      </defs>
      <polygon points="990,20 1097,128 1097,245 960,240 820,218" fill="url(#goldFade)"/>
      <path d="M0 0 H228 C275 45 292 165 242 256 L240 323 H0 Z" fill="url(#panelGreen)"/>
      <path d="M228 0 C275 45 292 165 242 256" fill="none" stroke="url(#goldEdge)" stroke-width="5"/>
      <path d="M236 258 Q640 195 1097 268 V323 H236 Z" fill="#1c2621"/>
      <path d="M236 258 Q640 195 1097 268" fill="none" stroke="#d4a04a" stroke-width="4"/>
    </svg>

    <div class="headshot" role="img" aria-label="Portrait of the studio owner in green scrubs holding an ultrasound probe"></div>

    <div class="eyebrow">MEET YOUR</div>
    <div class="headline">BABY</div>
    <span class="rule rule--left"></span>
    <div class="sub-script">Before Birth</div>
    <span class="rule rule--right"></span>

    <div class="scan-image" role="img" aria-label="4D ultrasound image of twin babies face to face"></div>

    <ul class="services">
      <li>4D ULTRASOUND</li>
      <li>EARLY GENDER</li>
      <li class="two-line">PREGNANCY<br>CONFIRMATION</li>
    </ul>

    <div class="brand-card">
      <div class="brand-name">4D Cradle Glimpse</div>
      <div class="brand-tagline">PRENATAL ULTRASOUND STUDIO</div>
    </div>

    <svg class="phone-icon" viewBox="0 0 44 44" aria-hidden="true">
      <circle cx="22" cy="22" r="20.5" fill="none" stroke="#d4a04a" stroke-width="2"/>
      <path d="M15 12.5c1-1 2.4-.8 3 .3l1.8 3.2c.5.9.2 1.8-.5 2.4l-1.1.9c.9 2.4 2.9 4.6 5.4 5.7l.9-1.1c.6-.7 1.6-.9 2.4-.4l3.1 1.9c1 .6 1.2 2 .3 2.9l-1.4 1.4c-1 1-2.6 1.3-4 .7-5.300-2.2-9.4-6.4-11.4-11.7-.5-1.4-.2-2.9.8-3.9z" fill="#d4a04a"/>
    </svg>
    <div class="phone-number">850-471-5923</div>
    <div class="location">CEDAR COVE, SEALAND</div>
  </section>
</div>
</body>
</html>
```